Business Card Design

New business card design

Target Market(s)

Residential & Commercial Property Managers

Industry/Entity Type

Plumbing Services

Contact Information for Business Card

Name - Rowan Keddle, title - Director, Phone Number - 0431 286 517, email - rowan@tbk-plumbing.com.au, Company ABN - 73 215 904 386,

Font styles to use
Sans Serif

Colors
0054AA
0677BA
7BADD7
CADEEF
E8F1F8

```html
<!DOCTYPE html>
<html lang="en">
<head>
<meta charset="utf-8">
<title>TBK Plumbing Services – Business Card</title>
<link rel="stylesheet" href="https://fonts.googleapis.com/css2?family=Quicksand:wght@300&family=Roboto:wght@400;700&display=swap">
<style>
  :root{
    --page:#ececec;
    --card-dark:#1f242c;
    --accent:#00aeef;
    --paper:#ffffff;
    --ink:#4a4f57;
    --muted:#9aa1aa;
    --light:#f2f4f6;
  }
  *{box-sizing:border-box;margin:0;padding:0}
  html,body{width:1200px;height:900px;overflow:hidden;background:var(--page)}
  .canvas{position:relative;width:1200px;height:900px}
  .card{
    position:absolute;left:337px;width:526px;height:300px;
    background:var(--card-dark);border-radius:22px;overflow:hidden;
    border:3px solid var(--accent);
    box-shadow:0 10px 24px rgba(0,0,0,.18);
  }
  .card--front{top:110px}
  .card--back{top:490px}
  .brand{position:absolute;color:var(--light);font-family:"Quicksand",sans-serif;font-weight:300}
  .brand__name{display:block;font-size:86px;line-height:1;letter-spacing:2px}
  .brand__tagline{display:block;font-size:11px;letter-spacing:7px;margin-top:4px;color:var(--light)}
  .card--front .brand{left:48px;top:22px}
  .card--back .brand{left:60px;top:86px}
  .card--back .brand__name{font-size:104px}
  .holder{position:absolute;right:38px;top:138px;text-align:right;font-family:"Roboto",sans-serif}
  .holder__name{display:block;color:var(--accent);font-weight:700;font-size:23px;letter-spacing:.5px}
  .holder__title{display:block;color:var(--light);font-size:16px;margin-top:4px}
  .bands{position:absolute;left:0;bottom:0}
  .contact{position:absolute;left:26px;top:208px;font-family:"Roboto",sans-serif;font-size:15px;color:var(--ink);line-height:23px;list-style:none}
  .contact__label{color:var(--accent)}
  .contact__item{display:flex;align-items:center;gap:7px}
  .contact__icon{width:12px;height:12px;flex:none}
</style>
</head>
<body>
<main class="canvas">
  <section class="card card--front" aria-label="Business card front">
    <svg class="bands" width="520" height="294" viewBox="0 0 520 294" aria-hidden="true">
      <path d="M0 196 H300 Q318 196 318 214 V294 H0 Z" fill="var(--paper)"/>
      <path d="M344 208 H486 V180 H520 V294 H344 Z" fill="var(--accent)"/>
    </svg>
    <div class="brand">
      <span class="brand__name">tbk</span>
      <span class="brand__tagline">plumbing services</span>
    </div>
    <div class="holder">
      <span class="holder__name">ROWAN KEDDLE</span>
      <span class="holder__title">Director</span>
    </div>
    <ul class="contact">
      <li class="contact__item"><span class="contact__label">ABN:</span> 73 215 904 386</li>
      <li class="contact__item">
        <svg class="contact__icon" viewBox="0 0 12 12" aria-hidden="true"><path d="M2 1h3l1 3-2 1.2a6 6 0 0 0 2.8 2.8L8 6l3 1v3a1 1 0 0 1-1 1A9 9 0 0 1 1 2a1 1 0 0 1 1-1z" fill="var(--accent)"/></svg>
        0431 286 517
      </li>
      <li class="contact__item">
        <svg class="contact__icon" viewBox="0 0 12 12" aria-hidden="true"><rect x="0.5" y="2" width="11" height="8" rx="1" fill="var(--accent)"/><path d="M1 3l5 3.5L11 3" stroke="#fff" stroke-width="1.2" fill="none"/></svg>
        rowan@tbk-plumbing.com.au
      </li>
    </ul>
  </section>

  <section class="card card--back" aria-label="Business card back">
    <div class="brand">
      <span class="brand__name">tbk</span>
      <span class="brand__tagline">plumbing services</span>
    </div>
  </section>
</main>
</body>
</html>
```